Real Estate Company / Capital Needs Cards!

need business cards designed using the logos that were just designed by pixelbarn.

Reason: per designers request deadline extended 1 day…thank you.

Target Market(s)

Investors and clients looking to purchase real estate or invest in the business.

Industry/Entity Type

Business

Requirements
Must have
• two designs - one for the real estate logo and one for the capital logo, similar but slightly different.
Nice to have
• something to make it pop (perhaps on the back)
Should not have
• much color

```html
<!DOCTYPE html>
<html lang="en">
<head>
<meta charset="utf-8">
<title>Norvale Real Estate — Business Cards</title>
<link href="https://fonts.googleapis.com/css2?family=Source+Sans+3:wght@400;600&display=swap" rel="stylesheet">
<style>
  :root {
    --stage: #e9e6e2;
    --card: #ffffff;
    --ink: #6d6e71;
    --ink-dark: #4a4a4c;
    --ink-soft: #8a8b8e;
    --band-light: #b3b4b6;
    --band-dark: #6f7073;
    --rule: #c9c9cb;
  }
  * { margin: 0; padding: 0; box-sizing: border-box; }
  html, body { width: 1200px; height: 498px; overflow: hidden; }
  body {
    background: var(--stage);
    font-family: "Source Sans 3", sans-serif;
    color: var(--ink);
    position: relative;
  }
  .card {
    position: absolute;
    top: 99px;
    width: 520px;
    height: 300px;
    background: var(--card);
    box-shadow: 0 6px 18px rgba(0,0,0,0.18);
    overflow: hidden;
  }
  .card--front { left: 50px; }
  .card--back { left: 630px; }

  .wordmark {
    display: flex;
    align-items: center;
    color: var(--ink);
    font-weight: 400;
    text-transform: uppercase;
    letter-spacing: 0.06em;
    white-space: nowrap;
  }
  .wordmark__square { background: var(--ink); flex: none; }

  .card--front .wordmark {
    position: absolute; top: 42px; left: 0; right: 0;
    justify-content: center; gap: 10px; font-size: 22px;
  }
  .card--front .wordmark__square { width: 30px; height: 30px; }

  .holder {
    position: absolute; top: 150px; right: 298px; text-align: right;
  }
  .holder__name { font-size: 19px; font-weight: 600; color: var(--ink-dark); line-height: 1.15; }
  .holder__title { font-size: 17px; color: var(--ink-soft); line-height: 1.2; }

  .divider {
    position: absolute; left: 232px; top: 136px; width: 1px; height: 96px; background: var(--rule);
  }

  .contact {
    position: absolute; left: 246px; top: 132px;
    list-style: none; font-size: 14px; color: var(--ink-dark); line-height: 1.4;
  }
  .contact li { display: flex; align-items: center; gap: 5px; }
  .contact .contact__phone { font-size: 16px; }
  .contact svg { width: 11px; height: 11px; fill: var(--ink); flex: none; }

  .bands { position: absolute; left: 0; bottom: 0; width: 520px; height: 60px; }

  .card--back .wordmark {
    position: absolute; top: 108px; left: 0; right: 0;
    justify-content: center; gap: 16px; font-size: 34px;
  }
  .card--back .wordmark__square { width: 48px; height: 48px; }
  .website {
    position: absolute; top: 200px; left: 0; right: 0; text-align: center;
    font-size: 15px; letter-spacing: 0.22em; color: var(--ink-dark);
  }
  .website strong { font-weight: 600; }
</style>
</head>
<body>

<section class="card card--front" aria-label="Business card front">
  <div class="wordmark"><span class="wordmark__square"></span>Norvale Real Estate</div>

  <div class="holder">
    <p class="holder__name">Your Name</p>
    <p class="holder__title">Title</p>
  </div>

  <div class="divider"></div>

  <ul class="contact">
    <li>Street Name, City Name</li>
    <li>State ZipCode</li>
    <li class="contact__phone">
      <svg viewBox="0 0 12 12"><path d="M3 1l2 2.5-1.2 1.2a7 7 0 0 0 3.5 3.5L8.5 7 11 9l-1.5 2C5 11 1 7 1 2.5z"/></svg>555-014-2730
    </li>
    <li class="contact__phone">
      <svg viewBox="0 0 12 12"><circle cx="6" cy="3.5" r="2.5"/><path d="M1 11.5c0-3 2.2-4.5 5-4.5s5 1.5 5 4.5z"/></svg>555-018-6412
    </li>
    <li>
      <svg viewBox="0 0 12 12"><path d="M1 4.5l5-3.5 5 3.5V11H1z"/><path d="M1.8 5l4.2 3 4.2-3" fill="none" stroke="#fff" stroke-width="1"/></svg>norvalerealestate@mailbox.com
    </li>
  </ul>

  <svg class="bands" viewBox="0 0 520 60" aria-hidden="true">
    <polygon points="0,50 520,38 520,60 0,60" fill="var(--band-light)"/>
    <polygon points="290,41 306,31 520,18 520,35 290,40.5" fill="var(--band-dark)"/>
  </svg>
</section>

<section class="card card--back" aria-label="Business card back">
  <div class="wordmark"><span class="wordmark__square"></span>Norvale Real Estate</div>
  <p class="website">www.<strong>norvalerealestate</strong>.com</p>
</section>

</body>
</html>
```